Business card design Needed for new logo / Construction business, home extensions and new builds

We need a business card design using our new logo files which i will attach to this project :)

We are a small construction business specialising in home extensions, new builds and property development. We are very ambitious and would appreciate professional and elegant designs for our new business card.

Very serious about using the services on MakerQuarry and recently acquired our new logo from here :)

Please get involved, i will feedback when i can as i am very busy but can respond daily, thanks

Target Market(s)

People that want to build onto their houses, new building developments or adding too their existing property

Industry/Entity Type

Construction

Contact Information for Business Card

Renwick Tolliver Construction, Lionel Ashby (Managing Director), Tel 07822254961, email - info@renwick-tolliver, www.renwick-tolliver.co.uk

Colors

Designer to choose colors to be used in the design.

Requirements
Must have
• I like a deep grey on the back please. A lot of you have provided black from and back, try mixing things up a little. The black looks cool 😎 Thanks

```html
<!DOCTYPE html>
<html lang="en">
<head>
<meta charset="utf-8">
<title>Renwick Tolliver Construction – Business Card</title>
<link rel="stylesheet" href="https://fonts.googleapis.com/css2?family=Cinzel:wght@400;500;600&display=swap">
<style>
  :root {
    --backdrop: #b5b5b4;
    --deep-grey: #333333;
    --black: #000000;
    --paper: #ffffff;
    --ink: #2a2526;
    --gold-dark: #bf8419;
    --gold-light: #fcd88b;
    --gold-warm: #f7b733;
    --silver-light: #e6e7e8;
    --silver-dark: #9a9ea3;
    --brand-text: #d6d6d6;
  }
  html, body {
    margin: 0;
    padding: 0;
    width: 1200px;
    height: 850px;
    overflow: hidden;
    background: var(--backdrop);
  }
  .canvas {
    position: relative;
    width: 1200px;
    height: 850px;
  }
  .card {
    position: absolute;
    left: 324px;
    width: 553px;
    height: 330px;
    border-radius: 28px;
    overflow: hidden;
  }
  .card--front { top: 47px; background: var(--deep-grey); }
  .card--back  { top: 419px; background: var(--paper); }
  .card__shapes {
    position: absolute;
    inset: 0;
    width: 100%;
    height: 100%;
  }
  .brand {
    position: absolute;
    left: 150px;
    right: 0;
    top: 178px;
    text-align: center;
    font-family: "Cinzel", serif;
    font-weight: 500;
    color: var(--brand-text);
    letter-spacing: 0.5px;
  }
  .brand__name {
    display: block;
    font-size: 24px;
    line-height: 1.15;
  }
  .brand__line {
    display: block;
    font-size: 16px;
    letter-spacing: 1.5px;
    margin-top: 4px;
  }
  .holder {
    position: absolute;
    left: 64px;
    top: 40px;
    font-family: "Cinzel", serif;
    color: var(--ink);
  }
  .holder__name {
    margin: 0;
    font-size: 27px;
    font-weight: 500;
    line-height: 1.1;
  }
  .holder__role {
    margin: 2px 0 0 2px;
    font-size: 17px;
    font-weight: 400;
    letter-spacing: 0.5px;
  }
  .contacts {
    position: absolute;
    left: 65px;
    top: 142px;
    margin: 0;
    padding: 0;
    list-style: none;
    font-family: "Cinzel", serif;
    color: var(--ink);
    font-size: 16px;
    letter-spacing: 0.6px;
  }
  .contacts__item {
    display: flex;
    align-items: center;
    height: 23px;
    margin-bottom: 15px;
  }
  .contacts__item:nth-child(2) { margin-bottom: 12px; }
  .contacts__item:nth-child(3) { margin-bottom: 17px; }
  .contacts__icon {
    width: 23px;
    height: 23px;
    margin-right: 11px;
    flex: none;
  }
</style>
</head>
<body>
<div class="canvas">

  <section class="card card--front" aria-label="Card front">
    <svg class="card__shapes" viewBox="0 0 553 330" aria-hidden="true">
      <defs>
        <linearGradient id="goldFront" x1="0" y1="0.15" x2="0.6" y2="1">
          <stop offset="0" stop-color="var(--gold-dark)"/>
          <stop offset="0.42" stop-color="var(--gold-light)"/>
          <stop offset="0.72" stop-color="var(--gold-dark)"/>
          <stop offset="1" stop-color="var(--gold-warm)"/>
        </linearGradient>
        <linearGradient id="silverFront" x1="0" y1="0" x2="0" y2="1">
          <stop offset="0" stop-color="var(--silver-light)"/>
          <stop offset="0.45" stop-color="var(--silver-dark)"/>
          <stop offset="1" stop-color="var(--silver-light)"/>
        </linearGradient>
      </defs>
      <polygon points="0,0 130,0 53,113 0,37" fill="var(--black)"/>
      <polygon points="0,238 46,308 120,308 135,330 0,330" fill="url(#silverFront)"/>
      <polygon points="0,37 184,308 46,308 0,238" fill="url(#goldFront)"/>
    </svg>
    <div class="brand">
      <span class="brand__name">RENWICK TOLLIVER</span>
      <span class="brand__line">CONSTRUCTION</span>
    </div>
  </section>

  <section class="card card--back" aria-label="Card back">
    <svg class="card__shapes" viewBox="0 0 553 330" aria-hidden="true">
      <defs>
        <linearGradient id="goldBack" x1="1" y1="0.15" x2="0.4" y2="1">
          <stop offset="0" stop-color="var(--gold-dark)"/>
          <stop offset="0.42" stop-color="var(--gold-light)"/>
          <stop offset="0.72" stop-color="var(--gold-dark)"/>
          <stop offset="1" stop-color="var(--gold-warm)"/>
        </linearGradient>
        <linearGradient id="silverBack" x1="0" y1="0" x2="0" y2="1">
          <stop offset="0" stop-color="var(--silver-light)"/>
          <stop offset="0.45" stop-color="var(--silver-dark)"/>
          <stop offset="1" stop-color="var(--silver-light)"/>
        </linearGradient>
      </defs>
      <polygon points="553,0 423,0 500,113 553,37" fill="var(--black)"/>
      <polygon points="553,238 507,308 433,308 418,330 553,330" fill="url(#silverBack)"/>
      <polygon points="553,37 369,308 507,308 553,238" fill="url(#goldBack)"/>
    </svg>

    <div class="holder">
      <h1 class="holder__name">YOUR NAMER</h1>
      <p class="holder__role">Founder</p>
    </div>

    <ul class="contacts">
      <li class="contacts__item">
        <svg class="contacts__icon" viewBox="0 0 24 24" aria-hidden="true">
          <circle cx="12" cy="12" r="12" fill="var(--ink)"/>
          <path d="M12 5.5a4 4 0 0 0-4 4c0 3 4 8 4 8s4-5 4-8a4 4 0 0 0-4-4zm0 5.6a1.6 1.6 0 1 1 0-3.2 1.6 1.6 0 0 1 0 3.2z" fill="var(--paper)"/>
        </svg>
        <span>Your Adress</span>
      </li>
      <li class="contacts__item">
        <svg class="contacts__icon" viewBox="0 0 24 24" aria-hidden="true">
          <circle cx="12" cy="12" r="12" fill="var(--ink)"/>
          <rect x="6" y="8" width="12" height="8.5" fill="none" stroke="var(--paper)" stroke-width="1.2"/>
          <path d="M6 8l6 5 6-5M6 16.5l4.5-4.5M18 16.5l-4.5-4.5" fill="none" stroke="var(--paper)" stroke-width="1.2"/>
        </svg>
        <span>Your email</span>
      </li>
      <li class="contacts__item">
        <svg class="contacts__icon" viewBox="0 0 24 24" aria-hidden="true">
          <circle cx="12" cy="12" r="12" fill="var(--ink)"/>
          <g fill="none" stroke="var(--paper)" stroke-width="1.1">
            <circle cx="12" cy="12" r="6"/>
            <ellipse cx="12" cy="12" rx="2.6" ry="6"/>
            <path d="M6 12h12M7 9h10M7 15h10"/>
          </g>
        </svg>
        <span>Your website</span>
      </li>
      <li class="contacts__item">
        <svg class="contacts__icon" viewBox="0 0 24 24" aria-hidden="true">
          <circle cx="12" cy="12" r="12" fill="var(--ink)"/>
          <path d="M8.4 6.2l2 2.2c.3.4.3.9 0 1.2l-.9 1c.7 1.5 1.9 2.7 3.4 3.4l1-.9c.3-.3.8-.3 1.2 0l2.2 2c.4.3.4.9 0 1.3l-1.2 1.2c-.6.6-1.6.8-2.4.4-3-1.4-5.4-3.8-6.8-6.8-.4-.8-.2-1.8.4-2.4l1.2-1.2c.4-.4 1-.4 1.3 0z" fill="var(--paper)"/>
        </svg>
        <span>Your number telephone</span>
      </li>
    </ul>
  </section>

</div>
</body>
</html>
```